Pebble Pete''s Funhouse Website Revamp

We have a children's entertainment center that hasn't changed in 20 years and the site looks like it was created 20 years ago. We need a new, modern, clean site that pops. Attached is the new logo that should be used as a style guide.

Current site is: www.pebblepetesfun-example.com

Thanks!
Updates

Designers, thank you all for the amazing work. It was exciting to be able to go through and see all the creativity that came in. I have decided on a design but wanted to share my thanks and appreciation for your time. Warm regards, Morris

Target Market(s)

Mothers with children in the 2 - 14 range.

Industry/Entity Type

Entertainment

```html
<!DOCTYPE html>
<html lang="en">
<head>
<meta charset="utf-8">
<title>Pebble Pete's Funhouse</title>
<link href="https://fonts.googleapis.com/css2?family=Quicksand:wght@500;600;700&family=Arimo:wght@400&family=Kaushan+Script&display=swap" rel="stylesheet">
<style>
:root{
  --page-top:#f36a12;
  --page-bottom:#f8a030;
  --panel:#ffffff;
  --ink:#333333;
  --body:#555555;
  --accent:#f2200a;
  --nav-home:#c8140c;
  --nav-attr:#e0401a;
  --nav-parties:#5fb61e;
  --nav-pricing:#3bb38c;
  --nav-directions:#3f6fc0;
  --nav-contact:#b630c8;
  --logo-green:#2fbf2a;
}
*{box-sizing:border-box;margin:0;padding:0}
html,body{width:993px;height:1200px;overflow:hidden}
body{
  position:relative;
  font-family:"Arimo",Arial,sans-serif;
  background:linear-gradient(180deg,var(--page-top) 0%,var(--page-bottom) 100%);
}
a{text-decoration:none;color:inherit}
.logo{position:absolute;left:0;top:116px;width:993px;display:flex;justify-content:center;align-items:center;gap:14px}
.logo-mark{width:54px;height:54px;border-radius:50%;background:var(--logo-green)}
.logo-name{font-family:"Quicksand",sans-serif;font-weight:700;font-size:44px;line-height:54px;color:var(--logo-green)}
.panel{position:absolute;left:142px;top:238px;width:708px;height:712px;background:var(--panel);border-radius:16px}
.nav{position:absolute;left:156px;top:252px;display:flex;gap:2px}
.nav a{width:112px;height:36px;border-radius:3px;color:#fff;
  font-family:"Quicksand",sans-serif;font-weight:500;font-size:13px;display:flex;align-items:center;justify-content:center;
  box-shadow:inset 0 14px 0 rgba(255,255,255,.25);border:1px solid rgba(0,0,0,.25)}
.nav .home{background:var(--nav-home)}
.nav .attractions{background:var(--nav-attr)}
.nav .parties{background:var(--nav-parties)}
.nav .pricing{background:var(--nav-pricing)}
.nav .directions{background:var(--nav-directions)}
.nav .contact{background:var(--nav-contact)}
.hero{position:absolute;left:156px;top:301px;width:681px;height:270px;border-radius:4px;
  background:linear-gradient(90deg,#1c1c22 0%,#2b2a33 40%,#4e6d9a 62%,#c9477a 80%,#3a3038 100%)}
.hero-title{position:absolute;left:40px;top:54px;font-family:"Kaushan Script",cursive;color:#fff;font-size:32px;line-height:36px}
.hero-btn{position:absolute;left:40px;top:177px;width:129px;height:36px;background:var(--accent);color:#fff;
  font-family:"Quicksand",sans-serif;font-weight:600;font-size:16px;display:flex;align-items:center;justify-content:center;border-radius:2px}
.hero-arrows{position:absolute;right:16px;bottom:12px;display:flex;gap:3px}
.hero-arrows span{width:19px;height:19px;background:var(--accent)}
.col{position:absolute;top:598px}
.col h2{font-family:"Quicksand",sans-serif;font-weight:600;color:var(--ink);font-size:15px;line-height:20px;margin-bottom:11px}
.col h2.big{font-size:19px;line-height:24px;margin-bottom:10px}
.col p{font-size:8.6px;line-height:17px;color:var(--body)}
.col p+p{margin-top:17px}
.thumb{width:195px;height:95px;border-radius:3px;margin-bottom:14px}
.thumb.ride{background:linear-gradient(135deg,#3e7d24,#9bcf4a 50%,#2f5e1f)}
.thumb.carousel{background:linear-gradient(135deg,#8a4a24,#e0b06a 50%,#6a3a2a)}
.read-more{position:absolute;top:813px;width:76px;height:22px;background:var(--accent);color:#fff;font-size:9px;
  display:flex;align-items:center;justify-content:center;border-radius:2px}
.footer{position:absolute;left:156px;top:859px;width:681px;height:69px;background:var(--accent);border-radius:3px;color:#fff}
.footer-links{position:absolute;left:22px;top:19px;display:flex;gap:30px;font-size:9px}
.copyright{position:absolute;left:22px;top:39px;font-size:9px}
.social{position:absolute;right:22px;top:20px;display:flex;gap:8px}
.social span{width:23px;height:23px;border-radius:50%;background:#fff}
</style>
</head>
<body>
<div class="logo"><span class="logo-mark"></span><span class="logo-name">Pebble Pete's Funhouse</span></div>
<div class="panel"></div>
<nav class="nav">
  <a class="home">Home</a><a class="attractions">Attractions</a><a class="parties">Parties</a>
  <a class="pricing">Pricing</a><a class="directions">Directions</a><a class="contact">Contact</a>
</nav>
<section class="hero" role="img" aria-label="Photo of two children laughing in a bumper car">
  <div class="hero-title">Beat the<br>summer heat<br>Online offers</div>
  <div class="hero-btn">CLICK HERE</div>
  <div class="hero-arrows"><span></span><span></span></div>
</section>
<div class="col" style="left:157px;width:245px">
  <h2 class="big">Welcome To The Jungle!</h2>
  <p>Pebble Pete's Funhouse is the Riverside Valley's #1 indoor amusement park for young kids. We cater exclusively to children from infants to around 11 years old. Our climate controlled fun center offers a unique mix of seven different amusement park rides. Pebble Pete's also makes its own pizza.</p>
  <p>Pebble Pete's Funhouse is the Riverside Valley's #1 indoor amusement park for young kids. We cater exclusively to children from infants to around 11 years old. Our climate controlled fun center offers a unique mix of seven...</p>
</div>
<div class="col" style="left:422px;width:196px">
  <h2>Attractions</h2>
  <div class="thumb ride" role="img" aria-label="Photo of children on a jungle car ride"></div>
  <p>Pebble Pete's Funhouse is the Riverside Valley's #1 indoor amusement park for young kids. We cater exclusively to children from infants to around 11 years old. Our climate controlled...</p>
</div>
<div class="col" style="left:643px;width:196px">
  <h2>Pricing</h2>
  <div class="thumb carousel" role="img" aria-label="Photo of a child on a carousel horse"></div>
  <p>Pebble Pete's Funhouse is the Riverside Valley's #1 indoor amusement park for young kids. We cater exclusively to children from infants to around 11 years old. Our climate controlled...</p>
</div>
<a class="read-more" style="left:156px">Read more</a>
<a class="read-more" style="left:422px">Read more</a>
<a class="read-more" style="left:643px">Read more</a>
<footer class="footer">
  <div class="footer-links"><span>Home</span><span>Attractions</span><span>Parties</span><span>Pricing</span><span>Directions</span><span>Contact</span></div>
  <div class="copyright">Copyrights © 2014 . pebble Petes All rights reserved.</div>
  <div class="social"><span></span><span></span><span></span><span></span><span></span></div>
</footer>
</body>
</html>
```